Flyer Design for Wedding Showcase

We are a modern Australian Restaurant situated on the Swan River in Perth boasting beautiful city views. We require a DL size flyer one sided to promote our wedding open evening which we hold every year.

Heading: Corella Point Restaurant Wedding Showcase
19th September 2014 from 5pm to 8pm
Address: Corella Point Restaurant, 17 Brindle Parade, Wexton WA 6112
Contact for more information: 08 9561 7284

There is several suppliers showcasing every year and we also have cocktail food and wine tastings at the event. Clients will also have the opportunity to chat to the function coordinators from Corella Point Restaurant.

We would like a modern, elegant design with a warm feeling to it. Couples getting married should be able to relate and identify with this design.

Target Market(s)

Young couples looking to get married

Industry/Entity Type

Wedding

Colors
3276b5
cee9f5
85abd2
eea4c8

Requirements
Must have
• Must have the following blurb:
Corella Point Restaurant is Perth's premium wedding venue situated on the Swan River boasting beautiful views of the Perth city skyline.
Come and meet our team and some of our favorite wedding suppliers while enjoying this beautiful location and sampling some of the food and wine we offer.

Logo needs to be on flyer
Should not have
• hot pink

```html
<!DOCTYPE html>
<html lang="en">
<head>
<meta charset="utf-8">
<title>Wedding Showcase Flyer – Corella Point Restaurant</title>
<link rel="stylesheet" href="https://fonts.googleapis.com/css2?family=Crimson+Pro:wght@400;500&family=Pinyon+Script&display=swap">
<style>
  :root {
    --cream: #f2eee7;
    --cream-light: #f8f5f0;
    --ink: #2b211c;
    --brand-blue: #3276b5;
    --table-dark: #2e2d2c;
    --table-mid: #55504b;
    --candle-warm: #b08a5c;
    --bloom: #e7ead8;
  }
  html, body {
    margin: 0;
    padding: 0;
    width: 1200px;
    height: 2400px;
    overflow: hidden;
    background: var(--cream);
  }
  .flyer {
    position: relative;
    width: 1200px;
    height: 2400px;
    overflow: hidden;
    background: linear-gradient(135deg, var(--cream-light), var(--cream));
    color: var(--ink);
    font-family: "Crimson Pro", "Times New Roman", serif;
  }
  .hero-photo {
    position: absolute;
    left: 0;
    top: 0;
    width: 1200px;
    height: 1280px;
    background:
      radial-gradient(ellipse 420px 260px at 400px 560px, rgba(176,138,92,0.55), transparent 70%),
      radial-gradient(ellipse 300px 200px at 300px 380px, rgba(231,234,216,0.6), transparent 70%),
      linear-gradient(160deg, var(--table-mid), var(--table-dark) 70%);
  }
  .date-band {
    position: absolute;
    left: 0;
    top: 90px;
    width: 1200px;
    height: 170px;
    background: rgba(245, 241, 234, 0.96);
    text-align: center;
  }
  .date-band .event-date {
    margin: 38px 0 0;
    font-size: 50px;
    font-weight: 400;
    line-height: 1;
    letter-spacing: 1px;
  }
  .date-band .event-time {
    margin: 12px 0 0;
    font-size: 34px;
    line-height: 1;
  }
  .headline {
    position: absolute;
    left: 0;
    top: 1330px;
    width: 1200px;
    margin: 0;
    font-family: "Pinyon Script", cursive;
    font-weight: 400;
    color: var(--ink);
  }
  .headline .word {
    position: absolute;
    white-space: nowrap;
    line-height: 1;
  }
  .headline .word-wedding {
    left: 120px;
    top: 40px;
    font-size: 230px;
  }
  .headline .word-showcase {
    left: 290px;
    top: 275px;
    font-size: 230px;
  }
  .blurb {
    position: absolute;
    left: 90px;
    top: 1786px;
    width: 1020px;
    margin: 0;
    font-size: 33px;
    line-height: 43px;
    text-align: center;
  }
  .brand {
    position: absolute;
    left: 88px;
    top: 2170px;
    display: flex;
    align-items: center;
    gap: 16px;
    color: var(--brand-blue);
    font-size: 40px;
    font-weight: 500;
    letter-spacing: 3px;
    text-transform: uppercase;
  }
  .brand .brand-dot {
    width: 22px;
    height: 22px;
    border-radius: 50%;
    background: var(--brand-blue);
  }
  .contact {
    position: absolute;
    left: 524px;
    top: 2128px;
    line-height: 1;
  }
  .contact .label {
    margin: 0;
    font-size: 29px;
  }
  .contact .value {
    margin: 4px 0 0;
    font-size: 35px;
    line-height: 38px;
  }
  .contact .label + .value + .label {
    margin-top: 20px;
  }
</style>
</head>
<body>
  <main class="flyer">
    <div class="hero-photo" role="img" aria-label="Photograph of a wedding reception table set with white flowers, glass vases, lit tealight candles and wine glasses on a dark tablecloth"></div>

    <header class="date-band">
      <p class="event-date">19th September 2014</p>
      <p class="event-time">from 5pm to 8pm</p>
    </header>

    <h1 class="headline">
      <span class="word word-wedding">Wedding</span>
      <span class="word word-showcase">Showcase</span>
    </h1>

    <p class="blurb">Corella Point Restaurant is Perth's premium wedding venue situated on the Swan River boasting beautiful views of the Perth city skyline. Come and meet our team and some of our favorite wedding suppliers while enjoying this beautiful location and sampling some of the food and wine we offer.</p>

    <div class="brand">
      <span class="brand-name">Corella Point</span>
      <span class="brand-dot"></span>
    </div>

    <address class="contact" style="font-style: normal;">
      <p class="label">Address:</p>
      <p class="value">Corella Point Restaurant, 17<br>Brindle Parade, Wexton WA 6112</p>
      <p class="label">Contact for more information:</p>
      <p class="value">08 9561 7284</p>
    </address>
  </main>
</body>
</html>
```